TA BRAMLEY BUSINESS CARD DESIGN PROJECT

We need to utilize our logo that was expertly created on PixelHarbor and now need to match this with a business card design.

```html
<!DOCTYPE html>
<html lang="en">
<head>
<meta charset="utf-8">
<title>TA BRAMLEY Business Card</title>
<link rel="stylesheet" href="https://fonts.googleapis.com/css2?family=Montserrat:wght@400;500;700;800&display=swap">
<style>
  :root {
    --backdrop: #4a4a49;
    --card-black: #181818;
    --card-white: #ffffff;
    --brand-blue: #0c55ab;
    --text-light: #f2f2f2;
    --emboss: #2c2c2c;
  }
  * { box-sizing: border-box; margin: 0; padding: 0; }
  html, body { width: 1200px; height: 801px; overflow: hidden; }
  body {
    background: var(--backdrop);
    font-family: "Montserrat", sans-serif;
    position: relative;
  }
  .card {
    position: absolute;
    width: 520px;
    height: 297px;
    top: 252px;
    background: var(--card-black);
    overflow: hidden;
    box-shadow: 0 14px 30px rgba(0,0,0,.35);
  }
  .card--front { left: 50px; }
  .card--back { left: 630px; }
  .card__art { position: absolute; inset: 0; width: 100%; height: 100%; }
  .swoosh__outer { fill: var(--card-white); }
  .swoosh__band { fill: var(--brand-blue); }
  .swoosh__panel { fill: var(--card-white); }
  .swoosh__line { fill: none; stroke: var(--brand-blue); stroke-width: 2.5; stroke-linecap: round; }
  .card__edge {
    position: absolute; left: 0; right: 0; bottom: 0;
    height: 3px; background: var(--brand-blue);
  }
  .contact-block {
    position: absolute; left: 34px; top: 82px;
    color: var(--text-light);
  }
  .contact-block__marker {
    position: absolute; left: -34px; top: 16px;
    width: 26px; height: 30px; background: var(--brand-blue);
  }
  .contact-block__name {
    font-weight: 800; font-size: 21px; letter-spacing: .5px;
    color: var(--brand-blue); line-height: 1.1;
  }
  .contact-block__role { font-size: 13px; font-weight: 500; margin-top: 2px; }
  .contact-list { list-style: none; margin-top: 20px; }
  .contact-list li {
    display: flex; align-items: center; gap: 9px;
    font-size: 12.5px; line-height: 1.55;
  }
  .contact-list svg { width: 11px; height: 11px; flex: none; }
  .contact-block__address { font-size: 12.5px; line-height: 1.45; margin-top: 14px; }
  .brand-name {
    position: absolute; font-weight: 800; white-space: nowrap;
  }
  .brand-name--front {
    right: 30px; top: 62px; font-size: 23px; color: var(--brand-blue);
    letter-spacing: 2px;
  }
  .brand-name--back {
    left: 0; right: 0; top: 118px; text-align: center;
    font-size: 48px; color: var(--emboss); letter-spacing: 6px;
  }
</style>
</head>
<body>

<section class="card card--front">
  <svg class="card__art" viewBox="0 0 520 297" aria-hidden="true">
    <path class="swoosh__outer" d="M228 0 C275 8 282 150 330 210 C370 258 450 272 520 266 L520 0 Z"/>
    <path class="swoosh__band" d="M232 0 C278 10 286 148 334 204 C372 250 450 262 520 258 L520 0 Z"/>
    <path class="swoosh__panel" d="M238 0 C282 12 292 146 342 196 C380 236 450 246 520 246 L520 0 Z"/>
    <path class="swoosh__line" d="M294 46 C312 90 318 140 356 180 C388 204 430 212 478 212"/>
  </svg>
  <div class="brand-name brand-name--front">TA BRAMLEY</div>

  <div class="contact-block">
    <span class="contact-block__marker"></span>
    <p class="contact-block__name">LENA MARSH</p>
    <p class="contact-block__role">Managing Director</p>
    <ul class="contact-list">
      <li>
        <svg viewBox="0 0 12 12"><path d="M2 1h3l1 3-2 1a7 7 0 0 0 3 3l1-2 3 1v3c-6 0-9-3-9-9z" fill="#0c55ab"/></svg>
        123 456 789
      </li>
      <li>
        <svg viewBox="0 0 12 12"><rect x="0.5" y="2" width="11" height="8" fill="#0c55ab"/><path d="M1 2.5l5 4 5-4" stroke="#181818" fill="none"/></svg>
        info@yourmail.com
      </li>
      <li>
        <svg viewBox="0 0 12 12"><circle cx="6" cy="6" r="5.5" fill="#0c55ab"/><path d="M0.5 6h11M6 0.5c-3 3-3 8 0 11M6 0.5c3 3 3 8 0 11" stroke="#181818" fill="none" stroke-width=".8"/></svg>
        www.yourwebsite.com
      </li>
    </ul>
    <p class="contact-block__address">Your address, City<br>State, Zip 1234</p>
  </div>
  <span class="card__edge"></span>
</section>

<section class="card card--back">
  <div class="brand-name brand-name--back">TA BRAMLEY</div>
  <span class="card__edge"></span>
</section>

</body>
</html>
```